Tech business card design

We need an amazing business card design for our new business 'Pexla' a marketing tech startup based in Sydney, Australia. We provide an online marketplace for businesses to search and buy advertising media, connect with service providers and learn more about marketing. We wish to communicate 'cool tech', reliability and professionalism and design based around our logo.

Target Market(s)

Business Owners

Contact Information for Business Card

Name
Position
Email Address
Website
Phone Number

Font styles to use
Other font styles liked:
• Avenir & Avenir Next

Colors

Designer to choose colors to be used in the design.

```html
<!DOCTYPE html>
<html lang="en">
<head>
<meta charset="UTF-8">
<title>Pexla Business Card</title>
<link rel="stylesheet" href="https://fonts.googleapis.com/css2?family=Nunito+Sans:wght@400;600;800&display=swap">
<style>
  :root {
    --navy: #1b1f4b;
    --white: #ffffff;
    --backdrop: #e6e7ec;
    --muted: #8a8eb5;
    --divider: #4b5080;
  }
  * { margin: 0; padding: 0; box-sizing: border-box; }
  html, body { width: 1200px; height: 900px; overflow: hidden; }
  body {
    background: var(--backdrop);
    font-family: "Nunito Sans", "Avenir Next", Avenir, sans-serif;
    display: flex;
    flex-direction: column;
    align-items: center;
    justify-content: center;
    gap: 50px;
  }
  .card {
    width: 560px;
    height: 320px;
    border-radius: 22px;
    overflow: hidden;
    box-shadow: 0 14px 30px rgba(20, 22, 50, 0.25);
    position: relative;
  }
  .card-front { background: var(--navy); }
  .front-top {
    background: var(--white);
    height: 160px;
    position: relative;
  }
  .brand {
    position: absolute;
    left: 44px;
    bottom: 30px;
    display: flex;
    align-items: center;
    gap: 14px;
  }
  .brand-mark {
    width: 34px;
    height: 34px;
    background: var(--navy);
  }
  .brand-name {
    font-weight: 800;
    font-size: 44px;
    line-height: 1;
    color: var(--navy);
  }
  .holder {
    position: absolute;
    right: 34px;
    bottom: 16px;
    text-align: right;
    color: var(--navy);
  }
  .holder-name { font-weight: 800; font-size: 19px; letter-spacing: 0.3px; }
  .holder-role { font-weight: 600; font-size: 14px; }
  .front-bottom {
    display: flex;
    align-items: flex-end;
    padding: 0 44px 26px;
    color: var(--white);
    font-size: 15px;
    height: 160px;
  }
  .contact-list { list-style: none; line-height: 1.55; }
  .contact-list li { display: flex; align-items: center; gap: 8px; }
  .contact-list svg { width: 14px; height: 14px; flex: none; }
  .divider {
    width: 1px;
    height: 48px;
    background: var(--divider);
    margin: 0 26px 18px;
  }
  .address { line-height: 1.4; margin-bottom: 46px; }
  .card-back {
    background: var(--navy);
    display: flex;
    align-items: center;
    justify-content: center;
  }
  .back-brand {
    display: flex;
    align-items: center;
    gap: 18px;
  }
  .back-brand .brand-mark { width: 46px; height: 46px; background: var(--muted); }
  .back-brand .brand-name { font-size: 60px; color: var(--muted); }
</style>
</head>
<body>
  <section class="card card-front">
    <div class="front-top">
      <div class="brand">
        <span class="brand-mark" aria-hidden="true"></span>
        <span class="brand-name">Pexla</span>
      </div>
      <div class="holder">
        <div class="holder-name">JOHN SMITH</div>
        <div class="holder-role">Position</div>
      </div>
    </div>
    <div class="front-bottom">
      <ul class="contact-list">
        <li>
          <svg viewBox="0 0 16 16" aria-hidden="true"><path fill="#fff" d="M3.6 1.5l2.2 2.6-1.2 1.6c.9 2.1 2.6 3.8 4.7 4.7l1.6-1.2 2.6 2.2-1.5 2.1C7 13 3 9 1.5 3z"/></svg>
          012-345-6789
        </li>
        <li>
          <svg viewBox="0 0 16 16" aria-hidden="true"><rect x="1" y="3" width="14" height="10" fill="#fff"/><path d="M1 3l7 6 7-6M1 13l5-5M15 13l-5-5" stroke="#1b1f4b" stroke-width="1.2" fill="none"/></svg>
          info@pexla.com
        </li>
        <li>
          <svg viewBox="0 0 16 16" aria-hidden="true" fill="none" stroke="#fff" stroke-width="1.2"><circle cx="8" cy="8" r="6.5"/><ellipse cx="8" cy="8" rx="2.8" ry="6.5"/><path d="M1.5 8h13M2.5 5h11M2.5 11h11"/></svg>
          www.pexla.com
        </li>
      </ul>
      <div class="divider"></div>
      <div class="address">
        Street Name, City Name<br>
        Zipcode:012345
      </div>
    </div>
  </section>

  <section class="card card-back">
    <div class="back-brand">
      <span class="brand-mark" aria-hidden="true"></span>
      <span class="brand-name">Pexla</span>
    </div>
  </section>
</body>
</html>
```